Business Card Design for Technology Company

New business card design needed for technology company director.
Ideally, the design will fit the style and nature of the industry. We are a supplier of quality products and services, and we hope the design will give customers and suppliers this impression.

Target Market(s)

3D Printing Industry

Industry/Entity Type

Technology Equipment

Contact Information for Business Card

Name: Marcus Lin
Title: Director
Company address: Factory K4, 7B Harlowe Road, Springvale Victoria Australia 3150
Telephone: +61-3-8555 6413
Email: marcus.lin@vortalmake.com.au
Website: www.vortalmake.com.au

Requirements
Must have
• All information in business card details
• Company logo
• '3D Printers and 3D Print Filaments' at proper place
Nice to have
• Style to fit the industry
• Colour to fit logo

```html
<!DOCTYPE html>
<html lang="en">
<head>
<meta charset="utf-8">
<title>Vortal Make – Business Card</title>
<link href="https://fonts.googleapis.com/css2?family=Exo+2:wght@700&family=Lato:ital,wght@0,400;0,700;1,400&display=swap" rel="stylesheet">
<style>
  :root {
    --page: #d9d9d9;
    --blue: #1a8fd0;
    --blue-light: #2aa6e4;
    --blue-dark: #0b4f86;
    --orange: #f7941d;
    --orange-light: #ffb23a;
    --black: #16171a;
    --white: #ffffff;
    --ink: #4a4a4a;
    --silver: #c9ccd0;
  }
  html, body {
    margin: 0;
    width: 1125px;
    height: 1200px;
    overflow: hidden;
    background: var(--page);
    font-family: "Lato", sans-serif;
  }
  .canvas { position: relative; width: 1125px; height: 1200px; }
  .card {
    position: absolute;
    left: 150px;
    width: 825px;
    height: 473px;
    overflow: hidden;
    box-shadow: 0 2px 4px rgba(0,0,0,.25);
  }
  .card-front { top: 108px; background: var(--black); }
  .card-back {
    top: 619px;
    background: linear-gradient(135deg, #e8f1f8 0%, #fdf6ee 45%, #fbf3ea 70%, #f4f5f6 100%);
  }
  .front-art { position: absolute; inset: 0; width: 100%; height: 100%; }

  .contact { position: absolute; left: 51px; top: 98px; color: var(--white); }
  .contact-name {
    font-family: "Exo 2", sans-serif;
    font-weight: 700;
    font-size: 32px;
    color: var(--orange);
    margin: 0;
    line-height: 1;
    letter-spacing: .5px;
  }
  .contact-title { font-weight: 700; font-size: 20px; margin: 4px 0 0; }
  .contact-address { font-size: 19px; line-height: 25px; margin: 22px 0 0; font-style: normal; }
  .contact-list { list-style: none; padding: 0; margin: 18px 0 0; font-size: 19px; line-height: 27px; }
  .contact-list li { display: flex; align-items: center; gap: 8px; }
  .contact-list svg { width: 18px; height: 18px; flex: none; }

  .brand-front {
    position: absolute;
    left: 469px;
    top: 100px;
    width: 320px;
    text-align: center;
  }
  .brand-mark { display: inline-block; background: var(--orange); }
  .brand-front .brand-mark { width: 110px; height: 110px; }
  .brand-name {
    display: block;
    font-family: "Lato", sans-serif;
    font-weight: 700;
    letter-spacing: 4px;
    margin-top: 28px;
  }
  .brand-front .brand-name { color: var(--white); font-size: 34px; }

  .brand-back { position: absolute; left: 0; right: 0; top: 78px; text-align: center; }
  .brand-back .brand-mark { width: 170px; height: 170px; }
  .brand-back .brand-name { color: var(--ink); font-size: 30px; margin-top: 22px; }

  .tagline {
    position: absolute;
    left: 0; right: 0; top: 366px;
    display: flex; justify-content: center; align-items: center; gap: 10px;
    font-size: 19px; color: var(--ink);
  }
  .tagline::before, .tagline::after { content: ""; width: 58px; height: 1px; background: var(--ink); }
  .partners {
    position: absolute;
    left: 0; right: 0; top: 402px;
    display: flex; justify-content: center; align-items: center; gap: 6px;
    font-size: 18px; color: var(--ink); font-style: italic;
  }
  .partner-name { font-style: normal; font-weight: 700; color: var(--ink); }
  .flag { display: inline-block; width: 26px; height: 17px; background: #1f3a8a; }
</style>
</head>
<body>
<div class="canvas">

  <section class="card card-front">
    <svg class="front-art" viewBox="0 0 800 458" preserveAspectRatio="none" aria-hidden="true">
      <defs>
        <linearGradient id="panelBlue" x1="0" y1="0" x2="1" y2="1">
          <stop offset="0" stop-color="#1e7fc2"/>
          <stop offset=".6" stop-color="#1a8fd0"/>
          <stop offset="1" stop-color="#2aa6e4"/>
        </linearGradient>
        <linearGradient id="stripeOrange" x1="0" y1="0" x2="1" y2="0">
          <stop offset="0" stop-color="#f7941d"/>
          <stop offset="1" stop-color="#ffb23a"/>
        </linearGradient>
      </defs>
      <rect width="800" height="458" fill="#16171a"/>
      <polygon points="0,0 472,0 332,228 522,458 0,458" fill="#c9ccd0"/>
      <polygon points="0,0 462,0 322,228 512,458 0,458" fill="url(#stripeOrange)"/>
      <polygon points="0,0 446,0 306,228 490,458 0,458" fill="#0b4f86"/>
      <polygon points="0,0 440,0 300,228 482,458 0,458" fill="url(#panelBlue)"/>
      <polyline points="5,5 432,5 296,228 470,452 5,452 5,5" fill="none" stroke="#0b4f86" stroke-width="3"/>
    </svg>

    <div class="contact">
      <h1 class="contact-name">MARCUS LIN</h1>
      <p class="contact-title">DIRECTOR</p>
      <address class="contact-address">Factory K4, 7B<br>Harlowe Road, Springvale<br>Victoria, Australia 3150</address>
      <ul class="contact-list">
        <li><svg viewBox="0 0 24 24"><path fill="#f7941d" d="M6.6 10.8a15 15 0 0 0 6.6 6.6l2.2-2.2c.3-.3.7-.4 1-.2 1.1.4 2.3.6 3.6.6.6 0 1 .4 1 1V20c0 .6-.4 1-1 1A17 17 0 0 1 3 4c0-.6.4-1 1-1h3.5c.6 0 1 .4 1 1 0 1.3.2 2.5.6 3.6.1.3 0 .7-.2 1z"/></svg>+61-3-8555 6413</li>
        <li><svg viewBox="0 0 24 24"><rect x="2" y="5" width="20" height="14" fill="#f7941d"/><path d="M2 5l10 8 10-8" fill="none" stroke="#1a8fd0" stroke-width="1.8"/></svg>marcus.lin@vortalmake.com.au</li>
        <li><svg viewBox="0 0 24 24"><circle cx="12" cy="12" r="10" fill="#f7941d"/><path d="M2 12h20M12 2c3 3 3 17 0 20M12 2c-3 3-3 17 0 20" fill="none" stroke="#1a8fd0" stroke-width="1.4"/></svg>www.vortalmake.com.au</li>
      </ul>
    </div>

    <div class="brand-front">
      <span class="brand-mark"></span>
      <span class="brand-name">VORTAL MAKE</span>
    </div>
  </section>

  <section class="card card-back">
    <div class="brand-back">
      <span class="brand-mark"></span>
      <span class="brand-name">VORTAL MAKE</span>
    </div>
    <p class="tagline">Leading supplier 3D Filaments &amp; 3D Printers</p>
    <p class="partners">Authorised distributor <span class="partner-name">Filaro</span> Authorised reseller <span class="partner-name">Printvane</span> in <span class="flag" role="img" aria-label="Australian flag"></span></p>
  </section>

</div>
</body>
</html>
```